Business Card Design (NEW FILES)

ATTENTION: New vector files are available. Please update your design to reflect/use the new (better resolution) logo images.

Seeking a unique and professional business card design for a commercial drone photography/videography business. The layout should feature
the logo (attached) and include the following information:
Owen Tarrick
614-502-7738
www.skylarkreelworks.example
NRD Certified Remote Pilot

Owen Tarrick

```html
<!DOCTYPE html>
<html lang="en">
<head>
<meta charset="utf-8">
<title>Skylark Reelworks – Business Card</title>
<link href="https://fonts.googleapis.com/css2?family=Open+Sans:wght@400;600;700;800&display=swap" rel="stylesheet">
<style>
  :root {
    --stage: #232323;
    --card-white: #f4f4f4;
    --navy: #161a48;
    --navy-deep: #121640;
    --navy-light: #24328a;
    --orange: #e8874a;
  }
  * { box-sizing: border-box; margin: 0; padding: 0; }
  html, body { width: 1200px; height: 780px; overflow: hidden; background: var(--stage); }
  body { position: relative; font-family: "Open Sans", sans-serif; }

  .card {
    position: absolute;
    top: 235px;
    width: 540px;
    height: 309px;
    overflow: hidden;
    box-shadow: 0 14px 30px rgba(0,0,0,0.55);
  }
  .card--front { left: 40px; background: var(--card-white); }
  .card--back { left: 620px; background: var(--navy-deep); }

  .front-swoosh { position: absolute; inset: 0; width: 100%; height: 100%; }

  .brand {
    position: absolute;
    display: flex;
    align-items: center;
    gap: 10px;
    color: var(--navy);
    font-weight: 700;
    letter-spacing: 0.5px;
  }
  .brand__dot { border-radius: 50%; background: var(--orange); flex: none; }
  .card--front .brand { left: 150px; top: 36px; font-size: 26px; }
  .card--front .brand__dot { width: 22px; height: 22px; }

  .details {
    position: absolute;
    left: 44px;
    top: 102px;
    list-style: none;
    color: var(--navy);
    font-size: 13.5px;
    font-weight: 600;
    line-height: 22px;
  }
  .details li { display: flex; align-items: center; gap: 8px; }
  .details .icon { width: 13px; height: 13px; flex: none; }
  .details .plain { padding-left: 21px; }

  .person {
    position: absolute;
    right: 62px;
    top: 200px;
    text-align: right;
  }
  .person__name { font-size: 27px; font-weight: 800; line-height: 1.1; }
  .person__first { color: var(--orange); }
  .person__last { color: var(--navy); }
  .person__role { font-size: 14px; font-weight: 600; color: var(--navy); margin-top: 2px; }
  .person-bar {
    position: absolute;
    right: 0;
    top: 200px;
    width: 48px;
    height: 58px;
    background: var(--orange);
  }

  .card--back .brand { left: 50%; top: 50%; transform: translate(-50%, -50%); color: var(--card-white); font-size: 30px; }
  .card--back .brand__dot { width: 26px; height: 26px; }
  .back-arc { position: absolute; inset: 0; width: 100%; height: 100%; }
</style>
</head>
<body>

  <section class="card card--front" aria-label="Business card front">
    <svg class="front-swoosh" viewBox="0 0 540 309" aria-hidden="true">
      <path d="M0,203 Q250,218 335,292 Q245,236 0,224 Z" fill="var(--orange)"/>
      <path d="M0,232 Q240,248 345,309 L0,309 Z" fill="var(--navy)"/>
    </svg>

    <div class="brand">
      <span class="brand__dot"></span>
      <span class="brand__name">Skylark Reelworks</span>
    </div>

    <ul class="details">
      <li class="plain">NRD Certified Remote Pilot</li>
      <li class="plain">Fully Insured</li>
      <li>
        <svg class="icon" viewBox="0 0 16 16" aria-hidden="true">
          <path d="M4 1.5l2.2 2.6-1.3 1.7c.8 1.9 2.2 3.4 4.2 4.3l1.7-1.3 2.7 2.2-1.4 2.5C6.8 13.3 2.6 9 1.6 3z" fill="var(--orange)"/>
        </svg>
        614-502-7738
      </li>
      <li>
        <svg class="icon" viewBox="0 0 16 16" aria-hidden="true">
          <circle cx="8" cy="8" r="7" fill="var(--orange)"/>
          <path d="M1 8h14M8 1c-3 3.5-3 10.5 0 14M8 1c3 3.5 3 10.5 0 14" stroke="var(--card-white)" stroke-width="1.1" fill="none"/>
        </svg>
        www.skylarkreelworks.example
      </li>
    </ul>

    <div class="person">
      <p class="person__name"><span class="person__first">Owen</span> <span class="person__last">Tarrick</span></p>
      <p class="person__role">Owner</p>
    </div>
    <div class="person-bar"></div>
  </section>

  <section class="card card--back" aria-label="Business card back">
    <svg class="back-arc" viewBox="0 0 540 309" aria-hidden="true">
      <path d="M30,70 Q40,170 260,190" stroke="var(--navy-light)" stroke-width="3" fill="none"/>
    </svg>
    <div class="brand">
      <span class="brand__dot"></span>
      <span class="brand__name">Skylark Reelworks</span>
    </div>
  </section>

</body>
</html>
```